Business Cards for a law firm

Business cards for our law firm. Use our silhoette logo and OAK PARTNERS - check our website (www.oakpartners.example)

Contact Information for Business Card

our silhouette logo, OAK PARTNERS, 800-555-0147, Dorian Pemberton, dorian@oakpartners.example

Requirements
Must have
• our silhouette logo, OAK PARTNERS, 800-555-0147, Dorian Pemberton, dorian@oakpartners.example

```html
<!DOCTYPE html>
<html lang="en">
<head>
<meta charset="utf-8">
<title>Oak Partners business cards</title>
<link href="https://fonts.googleapis.com/css2?family=Montserrat:wght@400;500;600&family=Open+Sans:wght@400;700&display=swap" rel="stylesheet">
<style>
  :root {
    --navy: #23346b;
    --navy-soft: #3a4a80;
    --white: #ffffff;
    --ink: #1b1b1f;
    --backdrop: #3a3a3c;
  }
  * { margin: 0; padding: 0; box-sizing: border-box; }
  html, body { width: 1200px; height: 1200px; overflow: hidden; }
  body {
    background: var(--backdrop);
    display: flex;
    flex-direction: column;
    align-items: center;
    justify-content: center;
    gap: 40px;
    font-family: "Montserrat", sans-serif;
  }
  .card {
    position: relative;
    width: 945px;
    height: 540px;
    border-radius: 34px;
    overflow: hidden;
  }
  .card--front { background: var(--navy); }
  .card--back { background: var(--white); }

  .brand {
    position: absolute;
    display: flex;
    align-items: center;
    gap: 22px;
    font-family: "Montserrat", sans-serif;
    font-weight: 500;
    letter-spacing: 0.12em;
    white-space: nowrap;
  }
  .brand__mark { display: block; }
  .card--front .brand {
    left: 190px; top: 230px;
    font-size: 58px; color: var(--white);
  }
  .card--front .brand__mark { width: 52px; height: 52px; background: var(--white); }
  .card--back .brand {
    left: 70px; top: 96px;
    font-size: 34px; color: var(--navy);
    gap: 16px;
  }
  .card--back .brand__mark { width: 32px; height: 32px; background: var(--navy); }

  .holder {
    position: absolute;
    right: 60px; top: 48px;
    text-align: right;
  }
  .holder__name {
    font-family: "Open Sans", sans-serif;
    font-weight: 700;
    font-size: 36px;
    color: var(--navy);
  }
  .holder__role {
    font-family: "Open Sans", sans-serif;
    font-size: 18px;
    color: var(--ink);
  }

  .contact {
    position: absolute;
    left: 90px; top: 292px;
    list-style: none;
    font-family: "Montserrat", sans-serif;
    font-size: 19px;
    color: var(--ink);
  }
  .contact__item { display: flex; align-items: center; gap: 12px; height: 32px; }
  .contact__icon { width: 18px; height: 18px; flex: none; }

  .figure-area {
    position: absolute;
    right: 80px; top: 150px;
    width: 250px; height: 230px;
    border-radius: 20px;
    background: radial-gradient(ellipse at center, rgba(35,52,107,0.55), rgba(35,52,107,0) 72%);
  }
  .wave { position: absolute; inset: 0; }
</style>
</head>
<body>
  <section class="card card--front">
    <div class="brand"><span class="brand__mark"></span><span class="brand__name">OAK PARTNERS</span></div>
  </section>

  <section class="card card--back">
    <svg class="wave" viewBox="0 0 945 540" aria-hidden="true">
      <path d="M150 540 C 260 420, 420 380, 600 350 C 760 325, 880 280, 945 230 L945 540 Z" fill="var(--navy)"/>
      <path d="M230 490 C 330 410, 480 385, 620 360 C 770 333, 860 300, 915 250" fill="none" stroke="var(--white)" stroke-width="4"/>
      <path d="M520 360 C 680 330, 800 300, 870 230" fill="none" stroke="var(--navy)" stroke-width="3"/>
    </svg>

    <div class="figure-area" role="img" aria-label="Decorative figure area in navy"></div>

    <div class="brand"><span class="brand__mark"></span><span class="brand__name">OAK PARTNERS</span></div>

    <div class="holder">
      <div class="holder__name">Dorian Pemberton</div>
      <div class="holder__role">Lawyer</div>
    </div>

    <ul class="contact">
      <li class="contact__item">
        <svg class="contact__icon" viewBox="0 0 24 24"><path fill="var(--navy)" d="M6.6 10.8a15 15 0 0 0 6.6 6.6l2.2-2.2c.3-.3.7-.4 1-.2 1.1.4 2.3.6 3.6.6.6 0 1 .4 1 1V20c0 .6-.4 1-1 1A17 17 0 0 1 3 4c0-.6.4-1 1-1h3.5c.6 0 1 .4 1 1 0 1.3.2 2.5.6 3.6.1.3 0 .7-.2 1z"/></svg>
        <span>800-555-0147</span>
      </li>
      <li class="contact__item">
        <svg class="contact__icon" viewBox="0 0 24 24"><rect x="2" y="5" width="20" height="14" fill="var(--navy)"/><path d="M2 5l10 8 10-8" fill="none" stroke="var(--white)" stroke-width="1.6"/></svg>
        <span>dorian@oakpartners.example</span>
      </li>
      <li class="contact__item">
        <svg class="contact__icon" viewBox="0 0 24 24"><circle cx="12" cy="12" r="10" fill="var(--navy)"/><path d="M2 12h20M12 2c3 3 3 17 0 20M12 2c-3 3-3 17 0 20" fill="none" stroke="var(--white)" stroke-width="1.2"/></svg>
        <span>www.oakpartners.example</span>
      </li>
    </ul>
  </section>
</body>
</html>
```